1 Banner für Affiliate-Marketing (Börse/Trading)
Zielgruppe
Wir vermitteln Kunden an einen Broker. Die Kunden eröffnen Handelskonten, in denen sie selbständig Finanzprodukte (CFDs, Forex, Aktien, Edelmetalle,...) gehebelt handeln. Wir bieten dem Kunden eine Dienstleistung an, indem wir Broker vorauswählen, technischen Support liefern, bei der Kontoeröffnung unterstützen und auf Wunsch auch Trader ausbilden.
Zielgruppe: männlich, finanz- und risikoaffin, Spekulant
Aufgabenstellung
Wir benötigen 1 klickstarken Banner für das Affiliate-Marketing
Bannergröße: 300*250
Formate: GIF, PNG, JPG, Vektor
Gerne auch animierte Vorschläge, aber bitte nicht ausschließlich.
Zusätzliche Info, die verarbeitet werden kann (aber nicht muss): Kelvora Bank hat in 2016 bei 2 Kundenumfragen den Testsieg als bester Broker gewonnen.
Design ist frei und muss sich nicht an der Homepage orientieren - vielmehr suchen wir klickstarke Banner aus der Finanz-/Börsenwelt mit Bildern Ihrer Wahl.

```html
<!DOCTYPE html>
<html lang="de">
<head>
<meta charset="utf-8">
<title>Banner-Set – Bester Broker 2016</title>
<link rel="stylesheet" href="https://fonts.googleapis.com/css2?family=Raleway:ital,wght@1,500;1,800&family=Oswald:wght@500&display=swap">
<style>
  :root {
    --green: #5e9a1c;
    --green-light: #73b025;
    --green-dark: #2f5a0a;
    --navy: #0f2d52;
    --btn-top: #2e6ea9;
    --btn-bottom: #0c3866;
    --photo-dark: #0c1828;
    --photo-mid: #2b3f5a;
    --gold: #c9a866;
    --gold-light: #e6d09a;
    --white: #ffffff;
    --page: #ffffff;
  }
  * { box-sizing: border-box; margin: 0; padding: 0; }
  html, body { width: 1200px; height: 728px; overflow: hidden; background: var(--page); }
  .stage { position: relative; width: 1280px; height: 776px; transform: scale(0.9375); transform-origin: 0 0; }

  .banner {
    position: absolute; overflow: hidden;
    background: linear-gradient(180deg, var(--green-light), var(--green));
    box-shadow: 0 16px 14px -10px rgba(0,0,0,.35);
  }
  .banner .photo { position: absolute; inset: 0; }
  .photo--right { background: linear-gradient(90deg, var(--photo-dark) 0%, var(--photo-mid) 45%, var(--gold) 78%, var(--gold-light) 100%); }
  .photo--top { background: linear-gradient(180deg, var(--photo-dark) 0%, var(--photo-mid) 25%, var(--gold) 55%, var(--gold-light) 70%); }
  .banner svg.field { position: absolute; inset: 0; width: 100%; height: 100%; }

  .headline { position: absolute; color: var(--white); font-family: "Raleway", sans-serif; font-style: italic; line-height: 1.02;
    text-shadow: -1px -1px 0 var(--navy), 1px -1px 0 var(--navy), -1px 1px 0 var(--navy), 1px 1px 0 var(--navy), 0 2px 3px rgba(0,0,0,.4); }
  .headline .lead { font-weight: 500; display: block; }
  .headline .claim { font-weight: 800; display: block; }
  .headline .year { font-weight: 500; }
  .headline .year b { font-weight: 800; }

  .cta { position: absolute; display: flex; align-items: center; justify-content: center;
    background: linear-gradient(180deg, var(--btn-top), var(--btn-bottom));
    border-radius: 8px; color: var(--white); font-family: "Oswald", sans-serif; font-weight: 500; letter-spacing: .3px;
    box-shadow: 0 3px 4px rgba(0,0,0,.35); }
</style>
</head>
<body>
<div class="stage">

  <!-- 468 x 60 -->
  <div class="banner banner--468" style="left:126px;top:41px;width:468px;height:60px;">
    <div class="photo photo--right" role="img" aria-label="Münzstapel mit jungen Pflanzen vor Börsenkursen"></div>
    <svg class="field" viewBox="0 0 468 60" preserveAspectRatio="none">
      <path d="M0 0H345Q372 30 352 60H0Z" fill="var(--green-dark)"/>
      <path d="M0 0H333Q360 30 340 60H0Z" fill="var(--green)"/>
    </svg>
    <div class="headline" style="left:20px;top:9px;">
      <span class="lead" style="font-size:15px;">mehrfacher Testsieg als</span>
      <span class="claim" style="font-size:19px;">BESTER BROKER <span class="year" style="font-size:17px;">in <b>2016</b></span></span>
    </div>
    <div class="cta" style="left:370px;top:20px;width:80px;height:23px;font-size:11px;border-radius:5px;">MEHR INFO</div>
  </div>

  <!-- 120 x 600 -->
  <div class="banner banner--120" style="left:26px;top:141px;width:120px;height:600px;">
    <div class="photo photo--top" role="img" aria-label="Münzstapel mit jungen Pflanzen vor Börsenkursen"></div>
    <svg class="field" viewBox="0 0 120 600" preserveAspectRatio="none">
      <path d="M0 228Q70 222 120 250V600H0Z" fill="var(--green-dark)"/>
      <path d="M0 240Q70 232 120 258V600H0Z" fill="var(--green)"/>
    </svg>
    <div class="headline" style="left:7px;top:336px;">
      <span class="lead" style="font-size:18px;">mehrfacher<br>Testsieg als</span>
      <span class="claim" style="font-size:24px;margin-top:8px;">BESTER<br>BROKER</span>
      <span class="year" style="font-size:19px;">in <b>2016</b></span>
    </div>
    <div class="cta" style="left:5px;top:555px;width:110px;height:28px;font-size:15px;">MEHR INFO</div>
  </div>

  <!-- 160 x 600 -->
  <div class="banner banner--160" style="left:185px;top:141px;width:160px;height:600px;">
    <div class="photo photo--top" role="img" aria-label="Münzstapel mit jungen Pflanzen vor Börsenkursen"></div>
    <svg class="field" viewBox="0 0 160 600" preserveAspectRatio="none">
      <path d="M0 228Q90 220 160 250V600H0Z" fill="var(--green-dark)"/>
      <path d="M0 242Q90 232 160 258V600H0Z" fill="var(--green)"/>
    </svg>
    <div class="headline" style="left:16px;top:328px;">
      <span class="lead" style="font-size:21px;">mehrfacher<br>Testsieg als</span>
      <span class="claim" style="font-size:28px;margin-top:6px;">BESTER<br>BROKER</span>
      <span class="year" style="font-size:23px;">in <b>2016</b></span>
    </div>
    <div class="cta" style="left:8px;top:545px;width:144px;height:36px;font-size:20px;">MEHR INFO</div>
  </div>

  <!-- 300 x 250 -->
  <div class="banner banner--300" style="left:385px;top:172px;width:300px;height:250px;">
    <div class="photo photo--right" role="img" aria-label="Münzstapel mit jungen Pflanzen vor Börsenkursen"></div>
    <svg class="field" viewBox="0 0 300 250" preserveAspectRatio="none">
      <path d="M0 100Q130 70 300 110V250H0Z" fill="var(--green-dark)"/>
      <path d="M0 118Q130 78 300 118V250H0Z" fill="var(--green)"/>
    </svg>
    <div class="headline" style="left:25px;top:128px;">
      <span class="lead" style="font-size:20px;">mehrfacher Testsieg als</span>
      <span class="claim" style="font-size:28px;">BESTER BROKER</span>
      <span class="year" style="font-size:22px;">in <b>2016</b></span>
    </div>
    <div class="cta" style="left:183px;top:208px;width:108px;height:28px;font-size:15px;">MEHR INFO</div>
  </div>

  <!-- 500 x 500 -->
  <div class="banner banner--500" style="left:731px;top:93px;width:500px;height:500px;">
    <div class="photo photo--right" role="img" aria-label="Münzstapel mit jungen Pflanzen vor Börsenkursen"></div>
    <svg class="field" viewBox="0 0 500 500" preserveAspectRatio="none">
      <path d="M0 205Q220 160 500 215V500H0Z" fill="var(--green-dark)"/>
      <path d="M0 262Q200 160 500 215V500H0Z" fill="var(--green)"/>
    </svg>
    <div class="headline" style="left:58px;top:270px;">
      <span class="lead" style="font-size:29px;">mehrfacher Testsieg als</span>
      <span class="claim" style="font-size:41px;">BESTER BROKER</span>
      <span class="year" style="font-size:33px;">in <b>2016</b></span>
    </div>
    <div class="cta" style="left:280px;top:421px;width:203px;height:53px;font-size:30px;border-radius:12px;">MEHR INFO</div>
  </div>

  <!-- 728 x 90 -->
  <div class="banner banner--728" style="left:384px;top:641px;width:728px;height:90px;">
    <div class="photo photo--right" role="img" aria-label="Münzstapel mit jungen Pflanzen vor Börsenkursen"></div>
    <svg class="field" viewBox="0 0 728 90" preserveAspectRatio="none">
      <path d="M0 0H490Q525 45 505 90H0Z" fill="var(--green-dark)"/>
      <path d="M0 0H475Q512 45 490 90H0Z" fill="var(--green)"/>
    </svg>
    <div class="headline" style="left:28px;top:20px;">
      <span class="lead" style="font-size:20px;">mehrfacher Testsieg als</span>
      <span class="claim" style="font-size:26px;">BESTER BROKER <span class="year" style="font-size:22px;">in <b>2016</b></span></span>
    </div>
    <div class="cta" style="left:557px;top:27px;width:130px;height:35px;font-size:19px;">MEHR INFO</div>
  </div>

</div>
</body>
</html>
```